In-Design Template: Single-sided A3 Brochure

Hi In-Design Experts,

I am after an A3 template which is created using In-Design. It needs to be able to operate in CS3.

This template will be used as the basis for a brochure for a beautiful range of stationery. In order to help me with the layout of the brochure, I require a template to be created using "In-Design". The template that you will create will include Rectangle Frames that will allow me to easily insert my products.

As this template is hard to describe in words, I have attached a diagram of what I am actually after. This is an A3 brochure (created on a slightly bigger canvas). As you will see, the right side is an exact replica of the left side. In creating the brochure, think of beautiful shades of pinks - incorporating baby pinks and pastel pinks - elegant, classy and beautiful.

Further details provided below and in the attached files.

If you require any further information or have any questions, please let me know.

Looking forward to seeing your designs.

Target Market(s)

Women

Requirements
Must have
• Template must be created using "In-Design" and be able to operate in version CS3.
• Template information - In the supporting files, I have set out the following:
• - Size of template (Image A3 created on canvas size SRA3 (450 x 320mm) with crop marks
• - Location of all text areas
• - Location of the boxes for my products - Please use the "Rectangle Frame Tool" to allow me to insert products later on.
• Further Design Work - The template is the basis and I would then require your creativity for the following design work:
• - Text to be included at the top of each page - "Tuvelle" using Edwarian Script (or similar font style. Please use the pink tones described above.
• - Image - I have attached an image that I would like to include in some way. I am thinking of placing this in the corners of the brochure - but opened to ideas. The image is a picture of scattered leaves. The picture I have attached is in shades of purple, however, I would require the leaves in shades of Pink. I am open to how you use these leaves in the template/brochure. You definitely do not need to use the exact leaves as displayed but something similar would be perfect.

```html
<!DOCTYPE html>
<html lang="en">
<head>
<meta charset="utf-8">
<title>Tuvelle Stationery Brochure Template</title>
<link rel="stylesheet" href="https://fonts.googleapis.com/css2?family=Pinyon+Script&family=Tinos&display=swap">
<style>
  :root {
    --bleed-pink: #f8cbce;
    --page-white: #ffffff;
    --script-pink: #ec9ea8;
    --leaf-pink: #eba3b0;
    --leaf-peach: #ecc2ab;
    --frame-grey: #8c8c8c;
    --ink: #3a3a3a;
    --crop-black: #111111;
  }
  * { margin: 0; padding: 0; box-sizing: border-box; }
  html, body { width: 1200px; height: 880px; overflow: hidden; }
  body { background: var(--bleed-pink); position: relative; font-family: "Tinos", "Times New Roman", serif; }

  .crop-marks { position: absolute; inset: 0; width: 1200px; height: 880px; }
  .crop-marks line { stroke: var(--crop-black); stroke-width: 1.4; }

  .sheet {
    position: absolute; left: 46px; top: 51px; width: 1107px; height: 778px;
    background: var(--page-white); overflow: hidden;
  }

  .leaves { position: absolute; }
  .leaves-top {
    left: 0; top: 0; width: 1107px; height: 72px;
    background:
      radial-gradient(ellipse 90px 50px at 40px 30px, rgba(235,163,176,.75), transparent 70%),
      radial-gradient(ellipse 130px 30px at 180px 12px, rgba(236,194,171,.7), transparent 70%),
      radial-gradient(ellipse 160px 25px at 340px 8px, rgba(235,163,176,.55), transparent 70%),
      radial-gradient(ellipse 200px 60px at 520px 30px, rgba(235,163,176,.7), transparent 70%),
      radial-gradient(ellipse 120px 55px at 580px 45px, rgba(236,194,171,.65), transparent 70%),
      radial-gradient(ellipse 200px 28px at 780px 12px, rgba(235,163,176,.55), transparent 70%),
      radial-gradient(ellipse 150px 30px at 960px 14px, rgba(236,194,171,.6), transparent 70%),
      radial-gradient(ellipse 80px 70px at 1090px 40px, rgba(235,163,176,.75), transparent 70%);
  }
  .leaves-bottom-left {
    left: 0; bottom: 0; width: 120px; height: 34px;
    background: radial-gradient(ellipse 110px 34px at 20px 34px, rgba(235,163,176,.7), transparent 70%);
  }
  .leaves-bottom-centre {
    left: 390px; bottom: 0; width: 320px; height: 34px;
    background:
      radial-gradient(ellipse 170px 34px at 170px 34px, rgba(235,163,176,.7), transparent 70%),
      radial-gradient(ellipse 90px 24px at 90px 34px, rgba(236,194,171,.6), transparent 70%);
  }
  .leaves-bottom-right {
    right: 0; bottom: 0; width: 130px; height: 40px;
    background: radial-gradient(ellipse 120px 40px at 120px 40px, rgba(235,163,176,.75), transparent 70%);
  }

  .page-title {
    position: absolute; top: 20px; width: 300px; text-align: center;
    font-family: "Pinyon Script", cursive; font-size: 58px; line-height: 1;
    color: var(--script-pink); font-weight: 400;
  }
  .page-heading {
    position: absolute; top: 78px; width: 300px; text-align: center;
    font-size: 20px; color: var(--ink); font-weight: 400;
  }
  .page-footer {
    position: absolute; top: 750px; width: 300px; text-align: center;
    font-size: 20px; color: var(--ink);
  }
  .page-left .page-title, .page-left .page-heading, .page-left .page-footer { left: 124px; }
  .page-right .page-title, .page-right .page-heading, .page-right .page-footer { left: 682px; }

  .product-grid {
    position: absolute; top: 109px;
    display: grid; grid-template-columns: repeat(8, 53px); grid-template-rows: repeat(7, 78px);
    column-gap: 13.6px; row-gap: 14.4px;
  }
  .page-left .product-grid { left: 14px; }
  .page-right .product-grid { left: 572px; }

  .frame {
    border: 1px solid var(--frame-grey); background: var(--page-white);
    display: flex; flex-direction: column; justify-content: flex-end;
  }
  .frame-label {
    height: 12px; border-top: 1px solid var(--frame-grey);
    font-size: 7px; line-height: 11px; text-align: center; color: var(--ink); letter-spacing: .2px;
  }
</style>
</head>
<body>
  <svg class="crop-marks" viewBox="0 0 1200 880" aria-hidden="true">
    <line x1="20" y1="43" x2="35" y2="43"/><line x1="40" y1="24" x2="40" y2="38"/>
    <line x1="1165" y1="43" x2="1180" y2="43"/><line x1="1160" y1="24" x2="1160" y2="38"/>
    <line x1="20" y1="835" x2="35" y2="835"/><line x1="40" y1="841" x2="40" y2="855"/>
    <line x1="1165" y1="835" x2="1180" y2="835"/><line x1="1160" y1="841" x2="1160" y2="855"/>
  </svg>

  <main class="sheet">
    <div class="leaves leaves-top" role="img" aria-label="Scattered pink and peach leaves along the top edge"></div>
    <div class="leaves leaves-bottom-left" role="img" aria-label="Scattered pink leaves in the lower left corner"></div>
    <div class="leaves leaves-bottom-centre" role="img" aria-label="Scattered pink leaves along the lower centre edge"></div>
    <div class="leaves leaves-bottom-right" role="img" aria-label="Scattered pink leaves in the lower right corner"></div>

    <section class="page page-left">
      <h1 class="page-title">Tuvelle</h1>
      <h2 class="page-heading">Text Box</h2>
      <div class="product-grid">
        <div class="frame"><span class="frame-label">TEXT</span></div><div class="frame"><span class="frame-label">TEXT</span></div><div class="frame"><span class="frame-label">TEXT</span></div><div class="frame"><span class="frame-label">TEXT</span></div><div class="frame"><span class="frame-label">TEXT</span></div><div class="frame"><span class="frame-label">TEXT</span></div><div class="frame"><span class="frame-label">TEXT</span></div><div class="frame"><span class="frame-label">TEXT</span></div>
        <div class="frame"><span class="frame-label">TEXT</span></div><div class="frame"><span class="frame-label">TEXT</span></div><div class="frame"><span class="frame-label">TEXT</span></div><div class="frame"><span class="frame-label">TEXT</span></div><div class="frame"><span class="frame-label">TEXT</span></div><div class="frame"><span class="frame-label">TEXT</span></div><div class="frame"><span class="frame-label">TEXT</span></div><div class="frame"><span class="frame-label">TEXT</span></div>
        <div class="frame"><span class="frame-label">TEXT</span></div><div class="frame"><span class="frame-label">TEXT</span></div><div class="frame"><span class="frame-label">TEXT</span></div><div class="frame"><span class="frame-label">TEXT</span></div><div class="frame"><span class="frame-label">TEXT</span></div><div class="frame"><span class="frame-label">TEXT</span></div><div class="frame"><span class="frame-label">TEXT</span></div><div class="frame"><span class="frame-label">TEXT</span></div>
        <div class="frame"><span class="frame-label">TEXT</span></div><div class="frame"><span class="frame-label">TEXT</span></div><div class="frame"><span class="frame-label">TEXT</span></div><div class="frame"><span class="frame-label">TEXT</span></div><div class="frame"><span class="frame-label">TEXT</span></div><div class="frame"><span class="frame-label">TEXT</span></div><div class="frame"><span class="frame-label">TEXT</span></div><div class="frame"><span class="frame-label">TEXT</span></div>
        <div class="frame"><span class="frame-label">TEXT</span></div><div class="frame"><span class="frame-label">TEXT</span></div><div class="frame"><span class="frame-label">TEXT</span></div><div class="frame"><span class="frame-label">TEXT</span></div><div class="frame"><span class="frame-label">TEXT</span></div><div class="frame"><span class="frame-label">TEXT</span></div><div class="frame"><span class="frame-label">TEXT</span></div><div class="frame"><span class="frame-label">TEXT</span></div>
        <div class="frame"><span class="frame-label">TEXT</span></div><div class="frame"><span class="frame-label">TEXT</span></div><div class="frame"><span class="frame-label">TEXT</span></div><div class="frame"><span class="frame-label">TEXT</span></div><div class="frame"><span class="frame-label">TEXT</span></div><div class="frame"><span class="frame-label">TEXT</span></div><div class="frame"><span class="frame-label">TEXT</span></div><div class="frame"><span class="frame-label">TEXT</span></div>
        <div class="frame"><span class="frame-label">TEXT</span></div><div class="frame"><span class="frame-label">TEXT</span></div><div class="frame"><span class="frame-label">TEXT</span></div><div class="frame"><span class="frame-label">TEXT</span></div><div class="frame"><span class="frame-label">TEXT</span></div><div class="frame"><span class="frame-label">TEXT</span></div><div class="frame"><span class="frame-label">TEXT</span></div><div class="frame"><span class="frame-label">TEXT</span></div>
      </div>
      <p class="page-footer">Website Address</p>
    </section>

    <section class="page page-right">
      <h1 class="page-title">Tuvelle</h1>
      <h2 class="page-heading">Text Box</h2>
      <div class="product-grid">
        <div class="frame"><span class="frame-label">TEXT</span></div><div class="frame"><span class="frame-label">TEXT</span></div><div class="frame"><span class="frame-label">TEXT</span></div><div class="frame"><span class="frame-label">TEXT</span></div><div class="frame"><span class="frame-label">TEXT</span></div><div class="frame"><span class="frame-label">TEXT</span></div><div class="frame"><span class="frame-label">TEXT</span></div><div class="frame"><span class="frame-label">TEXT</span></div>
        <div class="frame"><span class="frame-label">TEXT</span></div><div class="frame"><span class="frame-label">TEXT</span></div><div class="frame"><span class="frame-label">TEXT</span></div><div class="frame"><span class="frame-label">TEXT</span></div><div class="frame"><span class="frame-label">TEXT</span></div><div class="frame"><span class="frame-label">TEXT</span></div><div class="frame"><span class="frame-label">TEXT</span></div><div class="frame"><span class="frame-label">TEXT</span></div>
        <div class="frame"><span class="frame-label">TEXT</span></div><div class="frame"><span class="frame-label">TEXT</span></div><div class="frame"><span class="frame-label">TEXT</span></div><div class="frame"><span class="frame-label">TEXT</span></div><div class="frame"><span class="frame-label">TEXT</span></div><div class="frame"><span class="frame-label">TEXT</span></div><div class="frame"><span class="frame-label">TEXT</span></div><div class="frame"><span class="frame-label">TEXT</span></div>
        <div class="frame"><span class="frame-label">TEXT</span></div><div class="frame"><span class="frame-label">TEXT</span></div><div class="frame"><span class="frame-label">TEXT</span></div><div class="frame"><span class="frame-label">TEXT</span></div><div class="frame"><span class="frame-label">TEXT</span></div><div class="frame"><span class="frame-label">TEXT</span></div><div class="frame"><span class="frame-label">TEXT</span></div><div class="frame"><span class="frame-label">TEXT</span></div>
        <div class="frame"><span class="frame-label">TEXT</span></div><div class="frame"><span class="frame-label">TEXT</span></div><div class="frame"><span class="frame-label">TEXT</span></div><div class="frame"><span class="frame-label">TEXT</span></div><div class="frame"><span class="frame-label">TEXT</span></div><div class="frame"><span class="frame-label">TEXT</span></div><div class="frame"><span class="frame-label">TEXT</span></div><div class="frame"><span class="frame-label">TEXT</span></div>
        <div class="frame"><span class="frame-label">TEXT</span></div><div class="frame"><span class="frame-label">TEXT</span></div><div class="frame"><span class="frame-label">TEXT</span></div><div class="frame"><span class="frame-label">TEXT</span></div><div class="frame"><span class="frame-label">TEXT</span></div><div class="frame"><span class="frame-label">TEXT</span></div><div class="frame"><span class="frame-label">TEXT</span></div><div class="frame"><span class="frame-label">TEXT</span></div>
        <div class="frame"><span class="frame-label">TEXT</span></div><div class="frame"><span class="frame-label">TEXT</span></div><div class="frame"><span class="frame-label">TEXT</span></div><div class="frame"><span class="frame-label">TEXT</span></div><div class="frame"><span class="frame-label">TEXT</span></div><div class="frame"><span class="frame-label">TEXT</span></div><div class="frame"><span class="frame-label">TEXT</span></div><div class="frame"><span class="frame-label">TEXT</span></div>
      </div>
      <p class="page-footer">Website Address</p>
    </section>
  </main>
</body>
</html>
```